Modern Verdell Tree Care Website

I need a website for a full service Tree Care company. The company provides tree pruning, tree removal, tree preservation, emergency services, stump grinding, and emergency tree services.

Target Market(s)

Customers that need tree services

Industry/Entity Type

Landscaping, Tree Services

Coding

Coded - Design and coding required

Number of Pages Required

5+ page

Font styles to use
Sans Serif

Requirements
Must have
• Good clean design that showcases the services the company provides.
Nice to have
• Services page; contact form, blog, home page, about page

```html
<!DOCTYPE html>
<html lang="en">
<head>
<meta charset="utf-8">
<title>Verdell Tree Care</title>
<link rel="stylesheet" href="https://fonts.googleapis.com/css2?family=Montserrat:wght@400;500;600;700;800&display=swap">
<style>
:root{
  --green:#7dc242;
  --green-dark:#5e9d2c;
  --orange:#f9ab38;
  --cream:#fef3e6;
  --ink:#2a2a2a;
  --text:#4a4a4a;
  --footer:#2b2b2b;
  --white:#ffffff;
}
*{box-sizing:border-box;margin:0;padding:0}
html,body{width:1200px;height:4280px;overflow:hidden}
body{position:relative;font-family:"Montserrat",sans-serif;color:var(--text);background:var(--white)}
.abs{position:absolute}
.btn{position:absolute;display:flex;align-items:center;justify-content:center;background:var(--green);color:var(--ink);font-weight:700;font-size:13px;border-radius:22px;letter-spacing:.3px;text-transform:uppercase}
.photo{position:absolute}
/* header */
.site-header{position:absolute;left:0;top:0;width:1200px;height:90px;background:var(--white)}
.brand{position:absolute;left:103px;top:30px;font-weight:800;font-size:26px;color:var(--green-dark);letter-spacing:1px;display:flex;align-items:center;gap:10px}
.brand-mark{width:16px;height:16px;background:var(--orange)}
.nav a{position:absolute;top:38px;font-size:14px;color:var(--ink);font-weight:500;text-decoration:none}
/* hero */
.hero{left:0;top:90px;width:1200px;height:620px;background:linear-gradient(135deg,#3f5a1e 0%,#6e8f2c 35%,#a4b83d 60%,#4c6a20 100%)}
.hero-text{position:absolute;right:198px;top:248px;text-align:right;color:var(--white)}
.hero-welcome{font-weight:700;font-size:28px;letter-spacing:1px}
.hero-name{font-weight:800;font-size:84px;line-height:1;margin-top:22px;letter-spacing:2px}
.hero-sub{font-weight:500;font-size:48px;letter-spacing:12px;margin-top:8px}
/* headings */
.kicker{font-weight:700;font-size:18px;color:var(--orange);text-transform:uppercase}
.title{font-weight:700;font-size:31px;color:var(--ink);text-transform:uppercase;letter-spacing:.5px}
.center{width:1200px;left:0;text-align:center}
/* about */
.about-badge{left:155px;top:795px;width:372px;height:370px;background:#f4f8ee;display:flex;align-items:center;justify-content:center}
.about-badge span{font-weight:700;font-size:30px;color:var(--green-dark)}
.about-copy{left:640px;top:792px;width:430px}
.about-lead{color:var(--orange);font-size:17.5px;line-height:25px;font-weight:500;margin-top:14px}
.about-body{font-size:13.5px;line-height:25px;margin-top:14px}
/* services */
.services{left:0;top:1245px;width:1200px;height:833px;background:var(--cream)}
.card{position:absolute;background:var(--white);box-shadow:0 2px 8px rgba(0,0,0,.08);text-align:center}
.card-title{position:absolute;left:0;width:100%;font-weight:700;font-size:17px;color:var(--orange)}
.blog-title{text-transform:uppercase}
.card-text{position:absolute;left:20px;right:20px;font-size:13.5px;line-height:23px}
.arrow{position:absolute;width:26px;height:26px}
/* cta */
.cta{left:0;top:2078px;width:1200px;height:520px;background:linear-gradient(120deg,#5b6a58 0%,#4a6b2a 30%,#395f2a 55%,#6e7a6e 80%,#4d6130 100%)}
.cta-text{color:var(--white);font-weight:700;text-transform:uppercase;text-shadow:0 2px 6px rgba(0,0,0,.4)}
/* contact */
.contact-bg{left:0;top:3210px;width:1200px;height:662px;background:linear-gradient(120deg,#7dc242 0%,#76b840 50%,#7dc242 100%)}
.contact-kicker{position:absolute;left:104px;top:3432px;font-weight:700;font-size:18px;color:var(--ink)}
.contact-title{position:absolute;left:104px;top:3463px;font-weight:700;font-size:29px;color:var(--ink);white-space:nowrap}
.contact-intro{position:absolute;left:104px;top:3507px;width:420px;font-size:15px;line-height:25px;color:#2f3a22}
.field{position:absolute;left:640px;width:455px;background:var(--white);border-radius:30px;font-size:16px;color:#555;padding:18px 20px}
.icon-dot{position:absolute;width:44px;height:44px;border-radius:50%;background:var(--orange)}
.contact-line{position:absolute;left:163px;font-weight:700;font-size:16px;line-height:26px;color:var(--ink)}
/* footer */
.footer{left:0;top:3872px;width:1200px;height:408px;background:var(--footer);color:var(--white)}
.foot-brand{position:absolute;left:105px;top:98px;font-weight:700;font-size:42px;color:var(--green);letter-spacing:2px;line-height:1.1}
.foot-head{position:absolute;font-weight:700;font-size:19px;text-transform:uppercase;letter-spacing:.5px}
.foot-link{position:absolute;left:534px;font-size:14px}
</style>
</head>
<body>

<header class="site-header">
  <div class="brand"><span class="brand-mark"></span>VERDELL TREE CARE</div>
  <nav class="nav">
    <a style="left:550px">Home</a>
    <a style="left:628px">Services</a>
    <a style="left:723px">Blog</a>
    <a style="left:791px">About</a>
    <a style="left:871px">Contact Us</a>
  </nav>
  <div class="btn" style="left:989px;top:28px;width:106px;height:39px;font-size:14px">Log In</div>
</header>

<section class="photo hero" role="img" aria-label="Arborist in safety gear climbing a large tree with ropes"></section>
<div class="hero-text">
  <div class="hero-welcome">WELCOME TO</div>
  <div class="hero-name">VERDELL</div>
  <div class="hero-sub">TREE CARE</div>
</div>
<div class="btn" style="left:862px;top:487px;width:140px;height:38px">Get Started</div>
<svg class="abs" style="left:0;top:590px" width="1200" height="160" viewBox="0 0 1200 160">
  <polygon points="0,3 1200,108 1200,160 0,160" fill="#e9e9e9"/>
  <polygon points="0,18 1200,122 1200,160 0,160" fill="#ffffff"/>
  <polygon points="0,22 340,45 0,156" fill="var(--orange)"/>
</svg>

<div class="abs about-badge" role="img" aria-label="Company emblem area"><span>Verdell Tree Care</span></div>
<div class="abs about-copy">
  <div class="kicker">About Us</div>
  <div class="title" style="margin-top:12px">Verdell Tree Care</div>
  <p class="about-lead">At Verdell Tree Care, we are more than just a tree service company, we are stewards of our beautiful trees.</p>
  <p class="about-body">With a passion deeply rooted in arboriculture, we embark on a mission to promote the health, beauty, and safety of your trees and landscapes.Whether it's expert tree trimming to enhance aesthetics, meticulous tree removal to mitigate hazards, or comprehensive tree health assessments to ensure safety,</p>
</div>
<div class="btn" style="left:640px;top:1092px;width:138px;height:36px">Read More</div>

<section class="abs services"></section>
<div class="abs center kicker" style="top:1370px">Our Services</div>
<div class="abs center title" style="top:1400px">What We Do</div>

<svg class="arrow" style="left:39px;top:1694px" viewBox="0 0 26 26"><circle cx="13" cy="13" r="13" fill="#333"/><path d="M17 13H9m3-4-4 4 4 4" stroke="#fff" stroke-width="2.4" fill="none" stroke-linecap="round" stroke-linejoin="round"/></svg>
<svg class="arrow" style="left:1136px;top:1694px" viewBox="0 0 26 26"><circle cx="13" cy="13" r="13" fill="#333"/><path d="M9 13h8m-3-4 4 4-4 4" stroke="#fff" stroke-width="2.4" fill="none" stroke-linecap="round" stroke-linejoin="round"/></svg>

<div class="card" style="left:103px;top:1473px;width:322px;height:473px">
  <div class="photo" role="img" aria-label="Arborist pruning branches at the top of a tree" style="left:8px;top:8px;width:306px;height:231px;background:linear-gradient(160deg,#a9c9e6,#6d8f55 60%,#3e5a2a);clip-path:polygon(0 0,100% 0,100% 80%,50% 100%,0 80%)"></div>
  <div class="card-title" style="top:263px">Tree Pruning</div>
  <div class="card-text" style="top:296px">Lorem ipsum dolor sit amet, consectetur adipiscing elit, sed do eiusmod tempor incididunt ut labore et dolore magna aliqua.</div>
  <div class="btn" style="left:92px;top:400px;width:138px;height:38px">Read More</div>
</div>
<div class="card" style="left:439px;top:1473px;width:322px;height:473px">
  <div class="photo" role="img" aria-label="Tree removal crew working on a large trunk" style="left:8px;top:8px;width:306px;height:231px;background:linear-gradient(160deg,#4a86c8,#7f9a4a 50%,#8b7350);clip-path:polygon(0 0,100% 0,100% 80%,50% 100%,0 80%)"></div>
  <div class="card-title" style="top:263px">Tree Removal</div>
  <div class="card-text" style="top:296px">Lorem ipsum dolor sit amet, consectetur adipiscing elit, sed do eiusmod tempor incididunt ut labore et dolore magna aliqua.</div>
  <div class="btn" style="left:92px;top:400px;width:138px;height:38px">Read More</div>
</div>
<div class="card" style="left:775px;top:1473px;width:322px;height:473px">
  <div class="photo" role="img" aria-label="Hands planting a young seedling in soil" style="left:8px;top:8px;width:306px;height:231px;background:linear-gradient(160deg,#c7b66a,#6b7a3a 50%,#3a2f22);clip-path:polygon(0 0,100% 0,100% 80%,50% 100%,0 80%)"></div>
  <div class="card-title" style="top:263px">Tree Preservation</div>
  <div class="card-text" style="top:296px">Lorem ipsum dolor sit amet, consectetur adipiscing elit, sed do eiusmod tempor incididunt ut labore et dolore magna aliqua.</div>
  <div class="btn" style="left:92px;top:400px;width:138px;height:38px">Read More</div>
</div>

<section class="photo cta" role="img" aria-label="Tree crew feeding branches into a wood chipper beside a work truck"></section>
<div class="abs center cta-text" style="top:2186px;font-size:33px;line-height:48px">Call Verdell for all your tree<br>care needs</div>
<div class="abs center cta-text" style="top:2298px;font-size:27px">Serving Maplewood and surrounding areas</div>
<div class="btn" style="left:525px;top:2360px;width:151px;height:37px">Call Us Today!</div>
<svg class="abs" style="left:0;top:2490px" width="1200" height="150" viewBox="0 0 1200 150">
  <polygon points="0,95 1200,0 1200,150 0,150" fill="#e9e9e9"/>
  <polygon points="0,108 1200,14 1200,150 0,150" fill="#ffffff"/>
  <polygon points="860,44 1200,14 1200,150" fill="var(--orange)"/>
</svg>

<div class="abs center kicker" style="top:2623px">Latest News</div>
<div class="abs center title" style="top:2652px">Our Blog</div>

<svg class="arrow" style="left:39px;top:2945px" viewBox="0 0 26 26"><circle cx="13" cy="13" r="13" fill="#333"/><path d="M17 13H9m3-4-4 4 4 4" stroke="#fff" stroke-width="2.4" fill="none" stroke-linecap="round" stroke-linejoin="round"/></svg>
<svg class="arrow" style="left:1136px;top:2945px" viewBox="0 0 26 26"><circle cx="13" cy="13" r="13" fill="#333"/><path d="M9 13h8m-3-4 4 4-4 4" stroke="#fff" stroke-width="2.4" fill="none" stroke-linecap="round" stroke-linejoin="round"/></svg>

<div class="card" style="left:103px;top:2731px;width:304px;height:447px">
  <div class="photo" role="img" aria-label="Gardener trimming a small tree with shears" style="left:0;top:0;width:304px;height:224px;background:linear-gradient(150deg,#c9d79a,#7ea64a 50%,#4c6b2c)"></div>
  <div class="card-title blog-title" style="top:250px">Lorem Ipsum Dolor Sit</div>
  <div class="card-text" style="top:284px;font-size:12.5px;line-height:22px">Lorem ipsum dolor sit amet, consectetur adipiscing elit, sed do eiusmod tempor incididunt ut labore et dolore magna aliqua.</div>
  <div class="btn" style="left:88px;top:380px;width:130px;height:38px">Read More</div>
</div>
<div class="card" style="left:447px;top:2731px;width:304px;height:447px">
  <div class="photo" role="img" aria-label="Arborist cutting limbs among dense green branches" style="left:0;top:0;width:304px;height:224px;background:linear-gradient(150deg,#5f8a2e,#8fb33f 50%,#3d5a22)"></div>
  <div class="card-title blog-title" style="top:250px">Lorem Ipsum Dolor Sit</div>
  <div class="card-text" style="top:284px;font-size:12.5px;line-height:22px">Lorem ipsum dolor sit amet, consectetur adipiscing elit, sed do eiusmod tempor incididunt ut labore et dolore magna aliqua.</div>
  <div class="btn" style="left:88px;top:380px;width:130px;height:38px">Read More</div>
</div>
<div class="card" style="left:789px;top:2731px;width:305px;height:447px">
  <div class="photo" role="img" aria-label="Worker trimming a tall hedge with a hedge trimmer" style="left:0;top:0;width:305px;height:224px;background:linear-gradient(150deg,#9fb67a,#4f6e33 55%,#2f4a22)"></div>
  <div class="card-title blog-title" style="top:250px">Lorem Ipsum Dolor Sit</div>
  <div class="card-text" style="top:284px;font-size:12.5px;line-height:22px">Lorem ipsum dolor sit amet, consectetur adipiscing elit, sed do eiusmod tempor incididunt ut labore et dolore magna aliqua.</div>
  <div class="btn" style="left:88px;top:380px;width:130px;height:38px">Read More</div>
</div>

<section class="photo contact-bg" role="img" aria-label="Green tinted view of an arborist working in a tree"></section>
<svg class="abs" style="left:0;top:3205px" width="1200" height="160" viewBox="0 0 1200 160">
  <polygon points="0,0 1200,0 1200,55 0,146" fill="#ffffff"/>
  <polygon points="0,134 1200,45 1200,55 0,146" fill="#e9e9e9"/>
  <polygon points="0,6 340,115 0,144" fill="var(--orange)"/>
</svg>

<div class="contact-kicker">GET IN TOUCH</div>
<div class="contact-title">CONTACT VERDELL TREE CARE</div>
<p class="contact-intro">Call us today to see how we can help you with all of your tree needs:</p>

<div class="icon-dot" style="left:104px;top:3590px"></div>
<svg class="abs" style="left:115px;top:3601px" width="22" height="22" viewBox="0 0 24 24"><path d="M6.6 10.8a15 15 0 0 0 6.6 6.6l2.2-2.2c.3-.3.7-.4 1-.2 1.1.4 2.3.6 3.6.6.6 0 1 .4 1 1V20c0 .6-.4 1-1 1A17 17 0 0 1 3 4c0-.6.4-1 1-1h3.5c.6 0 1 .4 1 1 0 1.3.2 2.5.6 3.6.1.3 0 .7-.2 1z" fill="var(--ink)"/></svg>
<div class="contact-line" style="top:3580px">Call DALTON for a Free Estimate&nbsp; :<br>(555) 014-2739 Or (555) 019-9939</div>
<div class="icon-dot" style="left:104px;top:3664px"></div>
<svg class="abs" style="left:116px;top:3674px" width="20" height="24" viewBox="0 0 20 24"><path d="M10 1a7 7 0 0 0-7 7c0 5.2 7 14 7 14s7-8.8 7-14a7 7 0 0 0-7-7zm0 9.5A2.5 2.5 0 1 1 10 5.5a2.5 2.5 0 0 1 0 5z" fill="var(--ink)"/></svg>
<div class="contact-line" style="top:3654px">Location :<br>235, Verdell Tree Care<br>Lorem ipsum dolor sit 850</div>

<div class="field" style="top:3422px;height:60px">Name</div>
<div class="field" style="top:3490px;height:60px">E- Mail</div>
<div class="field" style="top:3560px;height:163px">Message</div>
<div class="btn" style="left:640px;top:3736px;width:140px;height:42px;background:transparent;border:2px solid var(--ink)">Submit</div>

<footer class="abs footer">
  <div class="foot-brand">VERDELL<br>TREE CARE</div>
  <div class="foot-head" style="left:534px;top:88px">Quick Links</div>
  <div class="foot-link" style="top:130px">Home</div>
  <div class="foot-link" style="top:160px">Services</div>
  <div class="foot-link" style="top:190px">Blog</div>
  <div class="foot-link" style="top:220px">About</div>
  <div class="foot-link" style="top:250px">Contact Us</div>
  <div class="foot-head" style="left:731px;top:88px">Newsletter</div>
  <p class="abs" style="left:735px;top:126px;width:300px;font-size:14px;line-height:25px">Lorem ipsum dolor sit amet, consectetur dolore magna aliqua.</p>
  <div class="abs" style="left:731px;top:190px;width:309px;height:39px;border:1.5px solid var(--white);border-radius:20px;font-size:14px;padding:10px 14px">Enter Email</div>
  <div class="btn" style="left:731px;top:246px;width:130px;height:37px;font-size:13px">Submit</div>
  <div class="abs" style="left:103px;top:333px;width:993px;height:1px;background:#777"></div>
  <div class="abs center" style="top:358px;font-size:13px">© 2024 VERDELL TREE CARE | ALL RIGHTS RESERVED</div>
</footer>

</body>
</html>
```